Banner für Immobilienmakler
Zielgruppe
Immobilienmakler, Immobilienverkauf mit Herz,
Aufgabenstellung
Verkauf von Häusern und Wohnungen, der Banner soll an einen Balkon oder einen Zaun angebracht werden mit dem Hinweis, dass das Haus Zu verkaufen ist.
Maße ca. 76 x 244cm
Es darf gerne frech und modern sein mit einem witzigen einladenden Spruch sein, sollte aber auch ansonsten zu meinem chicen Style passen (siehe Homepage www.karwendimmobilien.de) es soll sich abheben von anderen langweiligen Bannern.
Ggf soll die Plane auch noch an einem Tennisplatz angebracht werden

```html
<!DOCTYPE html>
<html lang="de">
<head>
<meta charset="utf-8">
<title>Karwend Immobilien – Banner Immobilienverkauf</title>
<link rel="stylesheet" href="https://fonts.googleapis.com/css2?family=DM+Serif+Display&family=Poppins:wght@300;600&display=swap">
<style>
  :root {
    --gold: #b8975e;
    --dark: #1d1d1d;
    --ink: #1a1a1a;
    --photo-green: #6f8f4e;
    --photo-sky: #9db6d6;
    --photo-room: #cfc7bd;
  }
  html, body { margin: 0; padding: 0; overflow: hidden; background: #fff; }
  .banner {
    position: relative;
    width: 1200px; height: 374px;
    overflow: hidden;
    font-family: "Poppins", sans-serif;
  }
  .contact-panel {
    position: absolute; left: 0; top: 0;
    width: 212px; height: 374px;
    background: var(--gold);
    color: var(--ink);
    text-align: center;
  }
  .brand-mark {
    position: absolute; left: 37px; top: 52px;
    width: 138px; height: 138px;
    border-radius: 50%;
    background: var(--dark);
    display: flex; align-items: center; justify-content: center;
  }
  .brand-mark span {
    color: var(--gold);
    font-weight: 300;
    font-size: 14px;
    line-height: 1.3;
    letter-spacing: 0.5px;
  }
  .agency-name {
    position: absolute; left: 0; right: 0; top: 223px;
    margin: 0;
    font-weight: 600; font-size: 12px;
  }
  .contact-list {
    position: absolute; left: 0; right: 0; top: 249px;
    margin: 0; padding: 0; list-style: none;
    font-weight: 300; font-size: 11.8px; line-height: 14.6px;
  }
  .contact-list li { white-space: nowrap; }
  .contact-list .contact-mail { font-size: 10.6px; letter-spacing: -0.1px; }
  .intro-panel {
    position: absolute; left: 212px; top: 0;
    width: 539px; height: 374px;
    background: var(--dark);
    color: var(--gold);
  }
  .headline {
    position: absolute; left: 30px; top: 71px;
    margin: 0;
    font-family: "DM Serif Display", serif;
    font-weight: 400;
    font-size: 55px; line-height: 1;
    letter-spacing: 0.2px;
    -webkit-text-stroke: 1px var(--gold);
    white-space: nowrap;
  }
  .tagline {
    position: absolute; left: 31px; top: 136px;
    margin: 0;
    font-weight: 300; font-size: 24.5px; line-height: 1.2;
  }
  .intro-text {
    position: absolute; left: 31px; top: 191px;
    width: 478px; margin: 0;
    font-weight: 300; font-size: 15.3px; line-height: 24.2px;
    text-align: justify; text-align-last: justify;
  }
  .photo { position: absolute; }
  .photo-apartments {
    left: 751px; top: 0; width: 224px; height: 187px;
    background: linear-gradient(180deg, var(--photo-sky), var(--photo-green));
  }
  .photo-house {
    left: 976px; top: 0; width: 224px; height: 187px;
    background: linear-gradient(180deg, var(--photo-sky), var(--photo-green));
  }
  .photo-living {
    left: 751px; top: 188px; width: 449px; height: 186px;
    background: var(--photo-room);
  }
</style>
</head>
<body>
<div class="banner">
  <aside class="contact-panel">
    <div class="brand-mark"><span>Karwend<br>Immobilien</span></div>
    <p class="agency-name">Karwend Immobilien</p>
    <ul class="contact-list">
      <li>Helene Karwend</li>
      <li>Tel.: 02241 - 48 48 270</li>
      <li>Mobil: 0176 - 3918240</li>
      <li class="contact-mail">Mail: mailrat@karwendimmobilien.de</li>
    </ul>
  </aside>

  <section class="intro-panel">
    <h1 class="headline">Immobilienverkauf</h1>
    <p class="tagline">mit herz und leidenschaft</p>
    <p class="intro-text">Wir begleiten Sie vom Erstkontakt bis zum Vertragsabschluss und stehen Ihnen in sämtlichen Fragen rund um Ihre Immobilie zur Verfügung. Nicht Massenabfertigung sondern die Konzen-<br>tration auf Ihre Wünsche und Vorstellungen ist unser Ziel. Ihre Zufriedenheit und Ihre Empfehlung sind die beste Werbung.</p>
  </section>

  <div class="photo photo-apartments" role="img" aria-label="Foto eines Mehrfamilienhauses mit Balkonen und Garten"></div>
  <div class="photo photo-house" role="img" aria-label="Foto eines weißen Einfamilienhauses mit Balkon und Garten"></div>
  <div class="photo photo-living" role="img" aria-label="Foto eines hellen Wohnzimmers mit Sofa und Esstisch"></div>
</div>
</body>
</html>
```